Business Card for a Jewellery Brand

Business card for an upscale jewellery brand. Attached is the brand logo and icon and color board. I am looking for two card versions: one for the founder and one is generic. The card should be elegant and convey upscale and premium feel. I am open to both square and rectangle card shapes.

Industry/Entity Type

Jewelry

Contact Information for Business Card

Two cards: (1) Sunela Parvaniya (Founder) (2) General
(1) Sunela Parvaniya card should have Name: Sunela Parvaniya, Title: Founder Email id: sunela@quiremo.com.au. Phone no: +61452913307
(2) Generic card should have Email id: info@quiremo.com.au. Phone no: +61436207518

Requirements
Must have
• Workmark
• ICON
• Phone no
• Email ID
• ABN: 58219740312 (Note: ABN is Business number in Australia)
• Website: www.quiremo.com.au
• Instagram: quiremo_jewellery
• Facebook: @quiremojewellery
Nice to have
• Tagline

```html
<!DOCTYPE html>
<html lang="en">
<head>
<meta charset="utf-8">
<title>Quiremo Business Cards</title>
<link href="https://fonts.googleapis.com/css2?family=Open+Sans:wght@400;600;700&display=swap" rel="stylesheet">
<style>
  :root {
    --page: #ece8e5;
    --charcoal: #2a2a2b;
    --paper: #ffffff;
    --blush: #e79a95;
    --ink: #1d1d1d;
    --white: #ffffff;
  }
  * { box-sizing: border-box; margin: 0; padding: 0; }
  html, body {
    width: 1200px; height: 900px; overflow: hidden;
    background: var(--page);
    font-family: "Open Sans", sans-serif;
  }
  .sheet {
    width: 1200px; height: 900px;
    display: flex; flex-direction: column; align-items: center; justify-content: center;
    gap: 40px;
  }
  .card {
    position: relative;
    width: 680px; height: 388px;
    border-radius: 4px;
    box-shadow: 0 6px 18px rgba(0,0,0,0.18);
    overflow: hidden;
  }
  .card--front {
    background: repeating-linear-gradient(0deg, #2e2e2f 0 2px, var(--charcoal) 2px 4px);
    display: flex; align-items: center; justify-content: center;
  }
  .wordmark {
    display: flex; align-items: center; gap: 18px;
    font-weight: 400; letter-spacing: 0.32em;
  }
  .wordmark__square { width: 22px; height: 22px; }
  .card--front .wordmark { color: var(--white); font-size: 52px; }
  .card--front .wordmark__square { background: var(--white); }

  .card--back { background: var(--paper); }
  .corner-mark { position: absolute; left: 0; top: 24px; }
  .holder { position: absolute; left: 66px; top: 22px; }
  .holder__name { color: var(--blush); font-weight: 700; font-size: 22px; line-height: 1.2; }
  .holder__title { color: var(--ink); font-size: 14px; }
  .abn { position: absolute; left: 32px; top: 112px; font-size: 16px; color: var(--ink); }
  .abn strong { font-weight: 700; }
  .contacts { position: absolute; left: 32px; top: 150px; list-style: none; }
  .contacts li {
    display: flex; align-items: center; gap: 12px;
    font-size: 16px; color: var(--ink); height: 26px;
  }
  .contacts svg { width: 14px; height: 14px; flex: none; }
  .card--back .wordmark {
    position: absolute; right: 60px; top: 150px;
    color: var(--blush); font-size: 46px;
  }
  .card--back .wordmark__square { background: var(--blush); width: 20px; height: 20px; }
  .band { position: absolute; left: 0; top: 0; }
</style>
</head>
<body>
<main class="sheet">
  <section class="card card--front" aria-label="Card front">
    <div class="wordmark"><span class="wordmark__square"></span><span>QUIREMO</span></div>
  </section>

  <section class="card card--back" aria-label="Card back">
    <svg class="corner-mark" width="56" height="48" viewBox="0 0 56 48">
      <polygon points="0,0 56,0 56,48 0,48" fill="var(--blush)"/>
      <polygon points="56,0 56,6 18,48 12,48" fill="var(--paper)"/>
    </svg>
    <div class="holder">
      <p class="holder__name">Sunela Parvaniya</p>
      <p class="holder__title">Founder</p>
    </div>
    <p class="abn"><strong>ABN:</strong> 58219740312</p>
    <ul class="contacts">
      <li><svg viewBox="0 0 14 14"><path d="M3 1 L5.5 1 L6.5 4 L5 5.3 Q6.3 8 8.7 9 L10 7.5 L13 8.5 L13 11 Q12.5 13 10.5 13 Q1 12 1 3.5 Q1 1 3 1Z" fill="var(--blush)"/></svg>+61452913307</li>
      <li><svg viewBox="0 0 14 14"><rect x="0.5" y="2.5" width="13" height="9" fill="var(--blush)"/><polyline points="0.5,2.5 7,8 13.5,2.5" fill="none" stroke="var(--paper)" stroke-width="1.2"/></svg>sunela@quiremo.com.au</li>
      <li><svg viewBox="0 0 14 14"><circle cx="7" cy="7" r="6.5" fill="var(--blush)"/><ellipse cx="7" cy="7" rx="2.6" ry="6" fill="none" stroke="var(--paper)" stroke-width="1"/><line x1="1" y1="7" x2="13" y2="7" stroke="var(--paper)" stroke-width="1"/></svg>www.quiremo.com.au</li>
      <li><svg viewBox="0 0 14 14"><rect x="0.5" y="0.5" width="13" height="13" fill="var(--blush)"/></svg>quiremo_jewellery</li>
      <li><svg viewBox="0 0 14 14"><circle cx="7" cy="7" r="6.5" fill="var(--blush)"/></svg>@quiremojewellery</li>
    </ul>
    <div class="wordmark"><span class="wordmark__square"></span><span>QUIREMO</span></div>
    <svg class="band" width="680" height="388" viewBox="0 0 680 388">
      <polygon points="0,316 268,316 252,338 0,338" fill="var(--blush)"/>
      <polygon points="286,316 680,316 680,366 250,366" fill="var(--blush)"/>
    </svg>
  </section>
</main>
</body>
</html>
```